IT Company needs Website for new Web and Mobile products for Sports and Fitness

Background:

We developed web based white label frontend web solution, backend services and white label mobile apps for to log, analyze, share and control sport and fitness activities. The name of this product suite is "Trevantix" (http://trevantix-example.com)

This products will be used by customers that provide platforms and community systems for sport and fitness. One of the major USP's is, that our technology i open for nearly all common formats, devices and apps out in the market. This means, you can just upload your data directly from device, file or app - e.G. Kestrel, Bolvane, Ravelo, StrideVault, Pacelumo, Zembra and much others.

Two current concrete examples/References

(1) MyQuorel
It's an international platform from quorel for runners. It provides individual training lans and a training log. MyQuorel uses the Backend Product "Trevantix Hub" (see http://hub.trevantix-example.net for a landing page) to integrate device, file and app support. Before this, every user has to track his training with manual inputs

(2) Paceharbor and fen-zine
Both are German customers. Paceharor is focused on runners. fen-zine is focused on Triatheletes. Both use the Product "Trevantix Web". This is a complete web solution with web based frontend solutions for athletes and coaches.

What do we need?
We need website layout for B2B for our products. We don't need lot's of pages. We need the pretty and nice layout, so we can derive the pages we need.

IMPORTANT
We don't talk about the webpages for the product itself (this will be a different project in future). We talk about a website, explaining the products)
Updates

Hi all,

we just start reviewing the first designs, and try to give feedback as detailed as possible. We attached a PDF document, to describe the the products a little bit more detailed. 

As written in the description, in the end we have two different sections. One is the usual stuff like "start page", "about", "contact", "disclaimer", "pricing", "blah...." and one will be the Developer Section, the "Tec Section". This ist aimed to developers (of our customers) that will integrate our products in there existing system or which will integrate our services in there own software.  This "pages" are more like "documentation", so easy to read and cool to look at (cause developers likes it cool, but straight)

Dear all,

we just do the final review. Cause this week is with heavy load, it takes some time...

Cheers

Odell

Target Market(s)

* Platforms and Communities for sport, health and fitness
* Gyms

Industry/Entity Type

Concrete

Font styles to use
Sans Serif

Requirements
Must have
• * Templates shall base on bootstrap. If not, it shall be easily realized on our site with bootstrap or out of the box "full responsive"

* HTML5 / CSS3
Nice to have
• PAGES
- Start Page
- Generic Template (from which we can derive additional pages)
- Contact Page
- Disclaimer Page
- Blog/News Page
- "About us" Page (can be combined with disclaimer)
- One Example product page (in end we have 3 products), shall show (if you need product details, let me know)
- product and it's description
- pricing information
- Add-Ons for the product
- Developer Section Page (Start Point for developers, where the finde "basic technical concepts and developer API's
- Example Developer Page for technical concept
- Example Developer Page for API

LOGO ISSUE
You can use an align to the Logo attached OR provide a new logo. The given logo is a logo for our own B2C Website http://trevantix-example.net. It's not really necessary, that the logo or the color must be used for the product website. Maybe it will be better if it's a complete new one, to avoid irritation between Trevantix as a B2B product and trevantix-example.net as a B2C platform.
Should not have
• No Flash and other proprietary technologies

```html
<!DOCTYPE html>
<html lang="en">
<head>
<meta charset="utf-8">
<title>Trevantix</title>
<link href="https://fonts.googleapis.com/css2?family=Ubuntu:wght@300;400;500;700&display=swap" rel="stylesheet">
<style>
:root{
  --orange:#f07f0d;
  --orange-light:#f39a31;
  --orange-dark:#e06a00;
  --ink:#3a3a3a;
  --text:#6f6f6f;
  --muted:#888;
  --band:#efefef;
  --footer:#3d3d3d;
  --green:#4aa62b;
  --white:#fff;
}
*{margin:0;padding:0;box-sizing:border-box}
html,body{width:1005px;height:1200px;overflow:hidden}
body{position:relative;background:var(--white);font-family:"Ubuntu",sans-serif;color:var(--text)}
.abs{position:absolute}
.top-band{left:0;top:0;width:1005px;height:237px;background:linear-gradient(#fafafa,var(--band));border-top:4px solid #e2e2e2}
.brand{left:72px;top:26px;display:flex;align-items:center;gap:10px}
.brand-dot{width:30px;height:30px;border-radius:50%;background:var(--orange)}
.brand-name{font-size:34px;font-weight:500;color:var(--ink);letter-spacing:.5px}
.main-nav{left:432px;top:48px;display:flex;align-items:center;font-size:16px;font-weight:300;color:#444}
.main-nav span.sep{margin:0 13px;color:#555}
.login{left:849px;top:42px;width:74px;height:32px;background:#222;color:#fff;border-radius:3px;font-size:15px;display:flex;align-items:center;justify-content:center;box-shadow:0 1px 2px rgba(0,0,0,.4)}
.hero{left:66px;top:101px;width:873px;height:352px;background:var(--orange-dark);border-radius:3px}
.hero-inner{left:75px;top:109px;width:855px;height:336px;background:radial-gradient(ellipse at 35% 40%,var(--orange-light),var(--orange) 70%)}
.hero-title{left:130px;top:180px;color:#fff;font-size:39px;font-weight:500;line-height:1}
.hero-sub{left:130px;top:221px;color:#fff;font-size:30px;font-weight:300;line-height:1}
.hero-text{left:131px;top:260px;color:#fff;font-size:13.5px;font-weight:300;line-height:18px;width:340px}
.btn-light{left:132px;top:306px;width:93px;height:27px;background:#fdf3e6;color:#8a4a08;border-radius:2px;font-size:12.5px;display:flex;align-items:center;justify-content:center}
.dots{left:134px;top:359px;display:flex;gap:4px}
.dots i{width:11px;height:11px;border-radius:50%;background:#f8c58a}
.device-dark{left:571px;top:164px;width:153px;height:323px;background:#1d1d1d;border-radius:22px}
.device-light{left:707px;top:132px;width:164px;height:347px;background:linear-gradient(#fdfdfd,#e8e8e8);border:1px solid #ccc;border-radius:24px}
.intro-title{left:70px;top:520px;font-size:34px;font-weight:300;color:var(--ink)}
.intro-sub{left:70px;top:560px;font-size:24px;font-weight:300;color:var(--muted)}
.intro-text{left:71px;top:596px;width:345px;font-size:12.5px;font-weight:300;line-height:21.3px;color:#555}
.btn-orange{left:70px;top:693px;width:81px;height:24px;background:linear-gradient(var(--orange-light),var(--orange-dark));color:#fff;border-radius:2px;font-size:11.5px;display:flex;align-items:center;justify-content:center}
.card{top:505px;width:239px;height:231px;border:1px solid #ddd;background:linear-gradient(#fff 70%,#f4f4f4)}
.card-media{position:absolute;left:10px;top:9px;width:220px;height:131px;border:1px solid #ccc}
.media-hand{background:linear-gradient(135deg,#e8eef0,#aab9c0 60%,#5a7c84)}
.media-run{background:linear-gradient(#d3d8dc,#8f9a8a 55%,#5d6a4b)}
.card-title{position:absolute;left:18px;top:151px;font-size:16px;color:var(--orange)}
.card-text{position:absolute;left:18px;top:174px;width:215px;font-size:12px;font-weight:300;line-height:15.5px;color:#666}
.play{position:absolute;left:92px;top:49px}
.divider{left:70px;top:766px;width:865px;height:1px;background:linear-gradient(90deg,transparent,#e6e6e6 20%,#e6e6e6 80%,transparent)}
.welcome-title{left:68px;top:808px;font-size:27px;font-weight:300;color:var(--ink)}
.welcome-text{left:68px;top:848px;width:600px;font-size:12.5px;font-weight:300;line-height:21.3px;color:var(--muted)}
.ticks{top:956px;list-style:none;font-size:12.8px;font-weight:300;color:#555}
.ticks li{display:flex;align-items:center;gap:8px;height:30px}
.vrule{left:677px;top:814px;width:1px;height:234px;background:#e6e6e6}
.news-title{left:704px;top:812px;font-size:22px;font-weight:300;color:var(--orange)}
.news{left:705px;top:850px;width:220px}
.news h3{font-size:12.5px;font-weight:400;color:#333;margin-bottom:5px}
.news p{font-size:11.5px;font-weight:300;line-height:17px;color:#888;margin-bottom:10px}
.footer{left:0;top:1097px;width:1005px;height:103px;background:var(--footer)}
.foot-nav{left:66px;top:1121px;display:flex;font-size:13px;color:#eee}
.foot-nav .sep{margin:0 12px}
.copyright{left:67px;top:1149px;font-size:10.5px;font-weight:300;color:#aaa}
.social{left:815px;top:1120px;display:flex;gap:8px}
.social i{width:22px;height:22px;border-radius:2px}
</style>
</head>
<body>
<div class="abs top-band"></div>

<header>
  <div class="abs brand"><span class="brand-dot"></span><span class="brand-name">Trevantix</span></div>
  <nav class="abs main-nav">
    <span>Home</span><span class="sep">|</span><span>About Us</span><span class="sep">|</span><span>Services</span><span class="sep">|</span><span>Solution</span><span class="sep">|</span><span>Contact</span>
  </nav>
  <div class="abs login">Login</div>
</header>

<section>
  <div class="abs hero"></div>
  <div class="abs hero-inner"></div>
  <h1 class="abs hero-title">Mauris vel lacus vitae</h1>
  <h2 class="abs hero-sub">Phasellus felis dolor scelerisque</h2>
  <p class="abs hero-text">Vivamus porttitor, g, purus nisi eleifend libero, a tempus libero lectus feugiat felis Morbit diam mauris</p>
  <div class="abs btn-light">Read More</div>
  <div class="abs dots"><i></i><i></i><i></i><i></i></div>
  <div class="abs device-light" role="img" aria-label="White smartphone showing a music app"></div>
  <div class="abs device-dark" role="img" aria-label="Black smartphone showing an app menu"></div>
</section>

<section>
  <h2 class="abs intro-title">Aliquam vehicula mau</h2>
  <h3 class="abs intro-sub">Phasellus felis dolor</h3>
  <p class="abs intro-text">Phasellus felis dolor, scelerisque a, tempus eget, lobortis id, libero. Donec scelerisque leo ac risus. Praesent sit amet est. In dictum, dolor eu dictum porttitor, enim felis viverra mi, eget luctus massa purus quis odio.</p>
  <div class="abs btn-orange">Read More</div>

  <article class="abs card" style="left:447px">
    <div class="card-media media-hand" role="img" aria-label="Hands holding a smartphone"></div>
    <h3 class="card-title">What We Do</h3>
    <p class="card-text">Aliquam nec erat at purus cursus interdum. Vestibulum ligula augue bibendum</p>
  </article>
  <article class="abs card" style="left:697px">
    <div class="card-media media-run" role="img" aria-label="Runner training outdoors in a field"></div>
    <svg class="play" width="36" height="36" viewBox="0 0 36 36"><circle cx="18" cy="18" r="17" fill="#111" stroke="#fff" stroke-width="1.5"/><path d="M14 11 L26 18 L14 25Z" fill="#fff"/></svg>
    <h3 class="card-title">Check Our Latest Video</h3>
    <p class="card-text">Aliquam nec erat at purus cursus interdum. Vestibulum ligula augue</p>
  </article>
</section>

<div class="abs divider"></div>

<section>
  <h2 class="abs welcome-title">Welcome to Our Website Mainpage</h2>
  <p class="abs welcome-text">Duis tincidunt lectus quis dui viverra vestibulum. Suspendisse vulputate aliquam dui. Nulla elementum dui ut augue. Aliquam vehicula mi at mauris. Maecenas placerat, nisl at consequat rhoncus, sem nunc gravida justo, quis eleifend arcu velit quis lacus. Morbi magna magna, tincidunt a, mattis non, imperdiet vitae, tellus. Sed odio est, auctor ac, sollicitudin in, consequat vitae, orci. Fusce id felis. Vivamus sollicitudin metus eget eros.</p>
  <ul class="abs ticks" style="left:75px">
    <li><svg width="18" height="18" viewBox="0 0 18 18"><circle cx="9" cy="9" r="9" fill="var(--green)"/><path d="M5 9.5l3 3 5-6" stroke="#fff" stroke-width="2" fill="none"/></svg>Duis tincidunt lectus quis dui viverra vestibulum.</li>
    <li><svg width="18" height="18" viewBox="0 0 18 18"><circle cx="9" cy="9" r="9" fill="var(--green)"/><path d="M5 9.5l3 3 5-6" stroke="#fff" stroke-width="2" fill="none"/></svg>Suspendisse vulputate aliquam dui.</li>
    <li><svg width="18" height="18" viewBox="0 0 18 18"><circle cx="9" cy="9" r="9" fill="var(--green)"/><path d="M5 9.5l3 3 5-6" stroke="#fff" stroke-width="2" fill="none"/></svg>Nulla elementum dui ut augue.</li>
  </ul>
  <ul class="abs ticks" style="left:385px;top:958px">
    <li><svg width="18" height="18" viewBox="0 0 18 18"><circle cx="9" cy="9" r="9" fill="var(--green)"/><path d="M5 9.5l3 3 5-6" stroke="#fff" stroke-width="2" fill="none"/></svg>Maecenas placerat nisl at consequat</li>
    <li><svg width="18" height="18" viewBox="0 0 18 18"><circle cx="9" cy="9" r="9" fill="var(--green)"/><path d="M5 9.5l3 3 5-6" stroke="#fff" stroke-width="2" fill="none"/></svg>Rhoncus sem nunc gravida justo</li>
    <li><svg width="18" height="18" viewBox="0 0 18 18"><circle cx="9" cy="9" r="9" fill="var(--green)"/><path d="M5 9.5l3 3 5-6" stroke="#fff" stroke-width="2" fill="none"/></svg>Morbi magna magna</li>
  </ul>

  <div class="abs vrule"></div>
  <h2 class="abs news-title">Latest News &amp; Blog</h2>
  <div class="abs news">
    <h3>Sand-sationeller Sonntag</h3>
    <p>Phasellus felis dolor scelerisque a tempus eget, lobortis id, libero Donec</p>
    <h3>Trevantix Talents &amp; Co. beim Ridgecross</h3>
    <p>Phasellus felis dolor scelerisque a tempus eget, lobortis id, libero Donec</p>
    <h3>Corvale Video zum Trevantix VardenRun</h3>
    <p>Phasellus felis dolor scelerisque tempus</p>
  </div>
</section>

<footer>
  <div class="abs footer"></div>
  <nav class="abs foot-nav">
    <span>HOME</span><span class="sep">|</span><span>ABOUT US</span><span class="sep">|</span><span>SERVICES</span><span class="sep">|</span><span>SOLUTION</span><span class="sep">|</span><span>CONTACT</span>
  </nav>
  <p class="abs copyright">© 2013 Company Name. All right reserved. Term of Use</p>
  <div class="abs social">
    <i style="background:#3b5a9a"></i><i style="background:#33aadd"></i><i style="background:#1a7bb5"></i><i style="background:#f07f0d"></i>
  </div>
</footer>
</body>
</html>
```